Mosquito and outdoor pest management

The uploaded logo must be integrated as the main theme of the card. I would like it to be modern and eye catching. Maybe some backround images or light silver metallic background.
Space enough at the base for contact info to be put in- phone numbers,emails,names,website.
Space on the back for short blog and lines for hand writing..calling card.
Commercial- golf courses, schools, outdoor function properties, pre event treatments.
Residential- retirement villages, townhome complexes and general houses
Management

```html
<!DOCTYPE html>
<html lang="en">
<head>
<meta charset="utf-8">
<title>Bayside Mosquito – Business Card</title>
<link rel="stylesheet" href="https://fonts.googleapis.com/css2?family=Marcellus&family=Marcellus+SC&display=swap">
<style>
  :root {
    --page-bg: #3b3b3b;
    --silver-light: #ffffff;
    --silver-mid: #dcdcdc;
    --silver-dark: #b9b9b9;
    --brand-red: #e8202c;
    --ink: #111111;
    --on-red: #111111;
    --rule: #7a7a7a;
  }
  * { margin: 0; padding: 0; box-sizing: border-box; }
  html, body {
    width: 1105px;
    height: 1200px;
    overflow: hidden;
    background: var(--page-bg);
  }
  .sheet {
    position: relative;
    width: 1105px;
    height: 1200px;
  }
  .card {
    position: absolute;
    left: 82px;
    width: 940px;
    height: 537px;
    overflow: hidden;
    background: radial-gradient(ellipse 55% 70% at 62% 50%, var(--silver-light) 0%, var(--silver-mid) 55%, var(--silver-dark) 100%);
  }
  .card--front { top: 43px; }
  .card--back { top: 620px; }
  .card__art {
    position: absolute;
    inset: 0;
    width: 100%;
    height: 100%;
  }

  /* Brand */
  .brand {
    position: absolute;
    right: 58px;
    top: 44px;
    display: flex;
    align-items: center;
    gap: 14px;
  }
  .brand__name {
    font-family: "Marcellus", serif;
    font-size: 42px;
    color: var(--ink);
    letter-spacing: 0.5px;
  }
  .brand__dot {
    width: 26px;
    height: 26px;
    border-radius: 50%;
    background: var(--brand-red);
  }

  /* Contact block on the red disc */
  .contact {
    position: absolute;
    left: 46px;
    top: 270px;
    color: var(--on-red);
  }
  .contact__name {
    font-family: "Marcellus SC", serif;
    font-size: 38px;
    letter-spacing: 1px;
    line-height: 1;
  }
  .contact__role {
    font-family: "Marcellus", serif;
    font-size: 28px;
    margin-top: 14px;
    line-height: 1;
  }
  .contact__list {
    list-style: none;
    margin-top: 24px;
  }
  .contact__item {
    display: flex;
    align-items: center;
    gap: 14px;
    font-family: "Marcellus", serif;
    font-size: 25px;
    line-height: 1;
    height: 40px;
    text-transform: uppercase;
  }
  .contact__item:first-child { text-transform: none; }
  .contact__icon {
    width: 24px;
    height: 24px;
    flex: none;
  }
</style>
</head>
<body>
<main class="sheet">

  <!-- Front -->
  <section class="card card--front" aria-label="Business card front">
    <svg class="card__art" viewBox="0 0 522 298" preserveAspectRatio="none" aria-hidden="true">
      <circle cx="124" cy="250" r="173" fill="var(--ink)"/>
      <circle cx="110" cy="249" r="170" fill="var(--brand-red)" stroke="#ffffff" stroke-width="2.5"/>
    </svg>

    <div class="brand">
      <span class="brand__name">Bayside Mosquito</span>
      <span class="brand__dot" aria-hidden="true"></span>
    </div>

    <div class="contact">
      <p class="contact__name">Daniel Reed</p>
      <p class="contact__role">CEO/Founder</p>
      <ul class="contact__list">
        <li class="contact__item">
          <svg class="contact__icon" viewBox="0 0 24 24" aria-hidden="true"><path fill="currentColor" d="M6.6 10.8c1.4 2.8 3.8 5.1 6.6 6.6l2.2-2.2c.3-.3.7-.4 1-.2 1.1.4 2.3.6 3.6.6.6 0 1 .4 1 1V20c0 .6-.4 1-1 1C10.6 21 3 13.4 3 4c0-.6.4-1 1-1h3.5c.6 0 1 .4 1 1 0 1.3.2 2.5.6 3.6.1.3 0 .7-.2 1z"/></svg>
          555 014 2290
        </li>
        <li class="contact__item">
          <svg class="contact__icon" viewBox="0 0 24 24" aria-hidden="true"><path fill="currentColor" d="M3 6h18v12H3z M3 6l9 7 9-7" stroke="var(--brand-red)" stroke-width="1.6"/></svg>
          hello@baysidemozzie.com
        </li>
        <li class="contact__item">
          <svg class="contact__icon" viewBox="0 0 24 24" aria-hidden="true"><circle cx="12" cy="12" r="10" fill="currentColor"/><path d="M7 8c2 0 3 1 3 3s2 2 2 4-1 3-1 4M14 5c0 2 1 3 3 3s2 2 3 2" fill="none" stroke="var(--brand-red)" stroke-width="1.5"/></svg>
          www.baysidemozzie.com
        </li>
      </ul>
    </div>
  </section>

  <!-- Back -->
  <section class="card card--back" aria-label="Business card back with writing lines">
    <svg class="card__art" viewBox="0 0 522 298" preserveAspectRatio="none" aria-hidden="true">
      <g stroke="var(--rule)" stroke-width="0.7" stroke-dasharray="1 1.6">
        <line x1="20" y1="39" x2="498" y2="39"/>
        <line x1="20" y1="71" x2="498" y2="71"/>
        <line x1="20" y1="102" x2="498" y2="102"/>
        <line x1="20" y1="132" x2="498" y2="132"/>
        <line x1="20" y1="168" x2="498" y2="168"/>
        <line x1="20" y1="201" x2="345" y2="201"/>
        <line x1="20" y1="240" x2="390" y2="240"/>
        <line x1="20" y1="270" x2="378" y2="270"/>
      </g>
      <circle cx="432" cy="232" r="30" fill="var(--brand-red)"/>
    </svg>
  </section>

</main>
</body>
</html>
```